Design my site www.brieflyledger.com

So here is what I am thinking in terms of design:

https://plenvo.com

https://www.skyluxair.com

http://kalvex.com/harbor-plaza-tower/

I want the theme to be white and blue (royal blue). I attached a paint picture of what I would like the site to look like in terms of placing the text. Generally, what I like about the sites above is that they are simple, you can navigate easily and have some kind of idea of what's going on by looking at the center (picture and motto). Let's establish a clear understanding of how the functional part of the site would look like. Please see the picture attached.

I want to keep it simple: On top would be the Name 'BRIEFLY ledger", somewhere to the right on top on the page would be 'Sign in" button.

In the center would be a picture (maybe a video) with the Motto (on top of it all in capital) OBSERVE NAVIGATE DECIDE and below would be the "sign up now"

Below the picture (like on kalvex.com site) or to the left on top of the page would be "About Us', "Press" "Contact Us' buttons.

Then once the user gets to his page his got 3 tabs " Press Headlines", "Events", " Briefings".

we would keep the same format I only have on the site, but separate for every Tab.

I do not want the user to get distracted. I also want him to be able to access the page though mobile phone and be able to get automatic updates just like Zorvan Pings without having to sign in daily.

The landing page must be minimalist yet with business/corporate feel where users can navigate easily and a "what you see is what you get" approach. You want an image or video (personally I prefer the video.. it does capture the users attention instantly, as long as it is an interesting video), with your taglines in it.

Sections available to public: About Us, Contact Us, Landing Page with Signup Option

Private: Public Sections + User Account Page, Tabs for (Events, Press Headlines, Briefings)

Target Market(s)

PR/media monitoring/diplomatic community

Coding

Coded - Design and coding required

Number of Pages Required

1 page

Font styles to use
Serif
Sans Serif

Colors
0255a3
ec1f27

Requirements
Must have
• a simple landing page, that is user friendly.
Nice to have
• a video with the explanation of how to navigate the site
Should not have
• too many colors, graphs etc.

```html
<!DOCTYPE html>
<html lang="en">
<head>
<meta charset="utf-8">
<title>BRIEFLY ledger</title>
<link href="https://fonts.googleapis.com/css2?family=Montserrat:wght@400;500&family=Open+Sans:wght@400&display=swap" rel="stylesheet">
<style>
  :root {
    --royal-blue: #0255a3;
    --nav-blue: #034488;
    --signal-red: #ec1f27;
    --white: #ffffff;
    --ink: #111111;
    --muted: #555555;
    --field-border: #c9c9c9;
    --hero-deep: #5e4c45;
    --hero-mid: #7d7878;
    --hero-light: #9a8b84;
  }
  * { box-sizing: border-box; margin: 0; padding: 0; }
  html, body { width: 1200px; height: 729px; overflow: hidden; background: var(--white); }
  body { font-family: "Open Sans", Arial, sans-serif; color: var(--ink); position: relative; }

  .site-header { position: absolute; left: 0; top: 0; width: 1200px; height: 91px; }
  .brand { position: absolute; left: 97px; top: 26px; font-family: "Montserrat", Arial, sans-serif; font-weight: 500; font-size: 31px; letter-spacing: 0.2px; color: var(--ink); }
  .sign-in { position: absolute; left: 972px; top: 29px; width: 129px; height: 37px; background: var(--signal-red); border-radius: 3px; color: var(--white); display: flex; align-items: center; justify-content: center; gap: 10px; font-size: 15px; text-decoration: none; }

  .hero { position: absolute; left: 0; top: 91px; width: 1200px; height: 490px; overflow: hidden; }
  .hero-backdrop { position: absolute; inset: 0; background:
      radial-gradient(ellipse 320px 200px at 1000px 300px, rgba(170,140,120,0.55), transparent 70%),
      radial-gradient(ellipse 260px 180px at 150px 120px, rgba(120,90,80,0.5), transparent 70%),
      linear-gradient(90deg, var(--hero-deep) 0%, var(--hero-mid) 40%, var(--hero-mid) 65%, var(--hero-light) 100%); }
  .motto { position: absolute; left: 0; top: 84px; width: 1200px; text-align: center; font-family: "Montserrat", Arial, sans-serif; font-size: 31px; font-weight: 400; letter-spacing: 0.5px; color: var(--white); }
  .play-button { position: absolute; left: 578px; top: 139px; }
  .slide-arrow { position: absolute; top: 218px; }
  .slide-arrow.prev { left: 14px; }
  .slide-arrow.next { left: 1150px; }

  .signup { position: absolute; left: 195px; top: 207px; width: 836px; height: 191px; background: var(--white); }
  .signup h2 { position: absolute; left: 0; top: 20px; width: 100%; text-align: center; font-family: "Montserrat", Arial, sans-serif; font-weight: 400; font-size: 21px; color: #333; }
  .field, .submit { position: absolute; width: 250px; height: 38px; font-family: "Open Sans", Arial, sans-serif; font-size: 12.5px; }
  .field { border: 1px solid var(--field-border); border-radius: 2px; padding: 0 13px; color: #666; background: var(--white); }
  .field::placeholder { color: #666; }
  .submit { background: var(--royal-blue); border: none; border-radius: 2px; color: var(--white); font-size: 14px; }
  .col-1 { left: 28px; } .col-2 { left: 293px; } .col-3 { left: 559px; }
  .row-1 { top: 63px; } .row-2 { top: 118px; }

  .section-nav { position: absolute; left: 0; top: 581px; width: 1200px; height: 69px; background: var(--royal-blue); display: flex; justify-content: center; align-items: center; gap: 8px; }
  .section-nav a { width: 110px; height: 35px; display: flex; align-items: center; justify-content: center; background: var(--nav-blue); color: var(--white); border-radius: 2px; font-family: "Montserrat", Arial, sans-serif; font-weight: 500; font-size: 13.5px; text-decoration: none; }
  .section-nav a.active { background: var(--signal-red); }

  .site-footer { position: absolute; left: 0; top: 650px; width: 1200px; height: 79px; }
  .copyright { position: absolute; left: 97px; top: 37px; font-size: 12px; color: var(--muted); }
  .social { position: absolute; left: 972px; top: 24px; display: flex; gap: 6px; }
  .social span { width: 27px; height: 27px; display: block; }
  .social .s1 { background: #283d8f; }
  .social .s2 { background: #55c1e7; }
  .social .s3 { background: #b0262b; }
  .social .s4 { background: #d34836; }
</style>
</head>
<body>
  <header class="site-header">
    <div class="brand">BRIEFLY ledger</div>
    <a class="sign-in" href="#">
      <svg width="15" height="15" viewBox="0 0 16 16" aria-hidden="true"><circle cx="5" cy="5" r="3.6" fill="none" stroke="#fff" stroke-width="2.2"/><path d="M7.5 7.5 L14 14 M11 11 L13 9 M12.6 12.6 L14.4 10.8" stroke="#fff" stroke-width="2.2" fill="none"/></svg>
      SIGN-IN
    </a>
  </header>

  <section class="hero">
    <div class="hero-backdrop" role="img" aria-label="Softly blurred background photo of a desk with reading glasses"></div>
    <h1 class="motto">OBSERVE NAVIGATE DECIDE</h1>
    <svg class="play-button" width="42" height="42" viewBox="0 0 42 42" aria-label="Play video"><circle cx="21" cy="21" r="21" fill="#fff"/><path d="M16 11 L31 21 L16 31 Z" fill="#222"/></svg>
    <svg class="slide-arrow prev" width="34" height="34" viewBox="0 0 34 34" aria-label="Previous slide"><circle cx="17" cy="17" r="17" fill="rgba(60,50,45,0.45)"/><path d="M20 9 L12 17 L20 25" stroke="#ccc" stroke-width="3" fill="none"/></svg>
    <svg class="slide-arrow next" width="34" height="34" viewBox="0 0 34 34" aria-label="Next slide"><circle cx="17" cy="17" r="17" fill="rgba(255,255,255,0.15)"/><path d="M14 9 L22 17 L14 25" stroke="rgba(255,255,255,0.5)" stroke-width="3" fill="none"/></svg>

    <form class="signup">
      <h2>Signup Now</h2>
      <input class="field col-1 row-1" type="text" placeholder="Name">
      <input class="field col-2 row-1" type="email" placeholder="Email">
      <input class="field col-3 row-1" type="tel" placeholder="Phone">
      <input class="field col-1 row-2" type="password" placeholder="Password">
      <input class="field col-2 row-2" type="password" placeholder="Re-Enter Password">
      <button class="submit col-3 row-2" type="button">SUBMIT</button>
    </form>
  </section>

  <nav class="section-nav">
    <a class="active" href="#">About Us</a>
    <a href="#">Press</a>
    <a href="#">Contact Us</a>
  </nav>

  <footer class="site-footer">
    <p class="copyright">Copyrights 2016 © Yoursite All Rights Reserved</p>
    <div class="social">
      <span class="s1" role="img" aria-label="Social link"></span>
      <span class="s2" role="img" aria-label="Social link"></span>
      <span class="s3" role="img" aria-label="Video channel link"></span>
      <span class="s4" role="img" aria-label="Social link"></span>
    </div>
  </footer>
</body>
</html>
```